Merrow Trade finance web design

We are a newly established business which provides invoice finance to Small Businesses in England and Wales.
Our approach is very much a funder where the small business owner can talk to the decision maker. We will guarantee on receipt of information, a decision within 24 hours.
We are not a bank so the look of the website need to be friendly but professional.
Have two types of people we are trying to attract to the website: 1) partners who are small business owners and 2) introducers who is accountants and commercial brokers who introduce us to the small businesses.
Currently no website, although domain has been reserved.
The design should be:
Professional
“Clean” Look
Designed to convey Trust and Authority.
Appeal to the small business owner.
Must incorporate:
Logo (attached)
Front page:Top tabs to other pages 1) About us 2) Services 3) Introducers 4) Contact us
Need picture and logo on page.
1) About us page- Room for talk about the company, the people and our critera.
2) Services page- We need for what invoice finance is, and 5 boxes for different services we will provide. (link on page to contact us)
3) Introducers page- We need a part for why become an introducer? Who we can help? Why we are different? (link on page to contact us)
4) Contact us page- Office address, email, tel and if possible a map and a contact me part which will email direct to us.
Text will be provided for the design, if we can see the setup of the website we will provide a part for each of the pages to support.
Styles we think convey the correct image:
www.dornelcapital.example
www.plivanlend.example
www.quorbacredit.example
Target Market(s)
Small business owners
Industry/Entity Type
Finance
Number of Pages Required
5+ page
Look and feel

```html
<!DOCTYPE html>
<html lang="en">
<head>
<meta charset="utf-8">
<title>Merrow Trade Finance</title>
<link rel="stylesheet" href="https://fonts.googleapis.com/css2?family=Roboto:wght@300;400;500;700&display=swap">
<style>
:root{
  --red:#e3373d;
  --red-dark:#c92a30;
  --ink:#2b2b2b;
  --grey:#8a8a8a;
  --light:#f4f4f4;
  --dark:#2a2a2a;
  --white:#ffffff;
}
*{box-sizing:border-box;margin:0;padding:0}
html,body{width:1200px;height:2908px;overflow:hidden;background:var(--white);font-family:"Roboto",Arial,sans-serif;color:var(--ink)}
.wrap{width:1044px;margin:0 auto;position:relative}
.btn{display:inline-block;background:var(--red);color:var(--white);font-size:20px;text-transform:uppercase;padding:18px 26px;text-decoration:none;letter-spacing:.3px}
.btn--ghost{background:transparent;border:2px solid var(--white)}
.accent{color:var(--red)}
.section-title{font-size:40px;font-weight:400;text-transform:uppercase;text-align:center}

/* header */
.site-header{height:115px}
.site-header .wrap{display:flex;justify-content:space-between;align-items:center;height:115px}
.brand{display:flex;align-items:center;gap:14px;font-size:44px;font-weight:700;color:var(--red)}
.brand-dot{width:22px;height:22px;border-radius:50%;background:var(--red)}
.call{display:flex;align-items:center;gap:20px;font-size:24px}
.call-icon{width:66px;height:66px;border-radius:50%;border:3px solid var(--red);display:flex;align-items:center;justify-content:center}

/* nav */
.main-nav{background:var(--red);height:62px}
.main-nav ul{list-style:none;display:flex;height:62px}
.main-nav a{display:flex;align-items:center;height:62px;padding:0 32px;color:var(--white);text-decoration:none;font-size:16px;text-transform:uppercase}
.main-nav .is-active a{background:#333}

/* hero */
.hero{height:521px;position:relative;background:linear-gradient(100deg,#e6e0d6 0%,#b9ab94 35%,#4c4a4a 65%,#232a38 100%)}
.hero .wrap{padding-top:136px}
.hero h1{font-size:50px;font-weight:400;color:#111;margin-bottom:14px}
.hero p{width:640px;font-size:15.5px;line-height:27px;color:#1b1b1b;margin-bottom:22px}

/* welcome */
.welcome{height:375px;text-align:center;padding-top:56px}
.welcome p{width:920px;margin:18px auto 22px;font-size:13.5px;line-height:27px;color:var(--grey)}

/* services */
.services{height:735px;background:linear-gradient(#2f2f2f,#242424);padding-top:58px}
.services .section-title{color:var(--white);margin-bottom:40px}
.service-grid{display:grid;grid-template-columns:repeat(3,333px);gap:24px 23px}
.service-card{height:254px}
.service-photo{height:196px}
.service-label{height:58px;background:var(--red);color:var(--white);display:flex;justify-content:space-between;align-items:center;padding:0 16px;font-size:20px;text-transform:uppercase}
.service-cta{height:254px;background:rgba(255,255,255,.1);display:flex;flex-direction:column;align-items:center;justify-content:center;color:var(--white)}
.service-cta .num{font-size:30px;margin:14px 0 18px}
.cta-icon{width:68px;height:68px;border-radius:50%;border:3px solid var(--red);display:flex;align-items:center;justify-content:center}

/* introducers */
.introducers{height:377px;background:linear-gradient(100deg,#d9444a,#e3575c);text-align:center;color:var(--white);padding-top:52px}
.introducers .section-title{color:#333}
.introducers .section-title span{color:var(--white)}
.introducers h3{font-size:20px;font-weight:400;margin:22px 0 10px}
.introducers p{width:900px;margin:0 auto 22px;font-size:14.5px;line-height:27px}

/* about + contact */
.info{height:515px;padding-top:54px}
.info .wrap{display:flex;justify-content:space-between}
.about{width:484px}
.info h2{font-size:38px;font-weight:400;text-transform:uppercase;margin-bottom:22px}
.about p{font-size:13.5px;line-height:27px;color:var(--grey);margin-bottom:8px}
.about .btn{margin-top:14px}
.contact{width:512px}
.field{height:48px;border:1px solid #d6d6d6;margin-bottom:7px;display:flex;justify-content:space-between;align-items:center;padding:0 14px;font-size:15px;color:var(--grey)}
.field--message{height:104px;align-items:flex-start;padding-top:16px}
.contact .btn{margin-top:3px;padding:18px 42px}

/* footer */
.site-footer{height:208px;background:var(--red);color:var(--white)}
.footer-top{display:flex;align-items:center;height:90px;border-bottom:1px solid rgba(255,255,255,.3)}
.footer-nav{display:flex;list-style:none;flex:1}
.footer-nav a{display:block;color:var(--white);text-decoration:none;font-size:14px;padding:14px 20px}
.footer-nav .is-active a{border:1px solid var(--white);padding:14px 40px;margin-right:14px}
.social{display:flex;gap:10px}
.social span{width:46px;height:46px;border-radius:50%;border:2px solid var(--white);display:block}
.social span:first-child{background:var(--white)}
.footer-head{font-size:17px;text-transform:uppercase;margin:16px 0 12px}
.footer-contacts{display:flex;align-items:center;font-size:13.5px;line-height:22px}
.fc{display:flex;align-items:center;gap:18px;margin-right:46px}
.fc-icon{width:52px;height:52px;border-radius:50%;border:2px solid var(--white);display:flex;align-items:center;justify-content:center;flex:none}
.fc-icon--solid{background:var(--white)}
.copy{margin-left:auto;width:200px;font-size:13.5px}
.copy b{color:#333;font-weight:400}
</style>
</head>
<body>

<header class="site-header">
  <div class="wrap">
    <div class="brand"><span class="brand-dot"></span>Merrow</div>
    <div class="call">CALL US ON:
      <span class="call-icon"><svg width="30" height="30" viewBox="0 0 24 24"><path fill="#e3373d" d="M6.6 10.8a15 15 0 0 0 6.6 6.6l2.2-2.2c.3-.3.7-.4 1-.2 1.1.4 2.3.6 3.6.6.6 0 1 .4 1 1V20c0 .6-.4 1-1 1A17 17 0 0 1 3 4c0-.6.4-1 1-1h3.5c.6 0 1 .4 1 1 0 1.3.2 2.5.6 3.6.1.3 0 .7-.2 1z"/></svg></span>
      123 456 7890</div>
  </div>
</header>

<nav class="main-nav">
  <div class="wrap">
    <ul>
      <li class="is-active"><a href="#">Home</a></li>
      <li><a href="#">About Us</a></li>
      <li><a href="#">Services</a></li>
      <li><a href="#">Introducers</a></li>
      <li><a href="#">Contact Us</a></li>
    </ul>
  </div>
</nav>

<section class="hero" role="img" aria-label="Photo of two businessmen reviewing documents at a desk">
  <div class="wrap">
    <h1>Merrow Trade Finance</h1>
    <p>Lorem Ipsum is simply dummy text of the printing and typesetting industry. Lorem Ipsum has been the industry's standard dummy text ever since the when an unknown printer took a galley of type and scrambled it to make a specimen book.</p>
    <a class="btn" href="#">Contact Us Know</a>
  </div>
</section>

<section class="welcome">
  <div class="wrap">
    <h2 class="section-title">Welcome to <span class="accent">Merrow</span></h2>
    <p>Lorem Ipsum is simply dummy text of the printing and typesetting industry. Lorem Ipsum has been the industry's standard dummy text ever since the 1500s, when an unknown printer took a galley of type and scrambled it to make a type specimen book.<br>It has survived not only five centuries. Lorem Ipsum is simply dummy text of the printing and typesetting industry. Lorem Ipsum has been the industry's standard dummy text ever since the 1500s, when an unknown printer took a galley of type and scrambled it to make a type specimen book. It has survived not only five centuries.</p>
    <a class="btn" href="#">Know More</a>
  </div>
</section>

<section class="services">
  <div class="wrap">
    <h2 class="section-title">Our <span class="accent">Services</span></h2>
    <div class="service-grid">
      <div class="service-card"><div class="service-photo" role="img" aria-label="Photo of a rising green bar chart model" style="background:linear-gradient(135deg,#eef2f0,#b7d39a 60%,#6aa03c)"></div><div class="service-label">Services One <span>&raquo;</span></div></div>
      <div class="service-card"><div class="service-photo" role="img" aria-label="Photo of business people meeting in a bright office" style="background:linear-gradient(135deg,#dfe8f1,#9fb6cf 60%,#4d6a8c)"></div><div class="service-label">Services Two <span>&raquo;</span></div></div>
      <div class="service-card"><div class="service-photo" role="img" aria-label="Photo of a calculator and pen on a financial chart" style="background:linear-gradient(135deg,#6c8fc4,#b8cbe6 55%,#eef3fa)"></div><div class="service-label">Services Three <span>&raquo;</span></div></div>
      <div class="service-card"><div class="service-photo" role="img" aria-label="Photo of a hand writing on financial documents" style="background:linear-gradient(135deg,#f1f3f6,#c3cfdc 60%,#5f7694)"></div><div class="service-label">Services Four <span>&raquo;</span></div></div>
      <div class="service-card"><div class="service-photo" role="img" aria-label="Photo of stacked gold coins" style="background:linear-gradient(135deg,#e9e4d8,#d1b064 55%,#8a6a25)"></div><div class="service-label">Services Five <span>&raquo;</span></div></div>
      <div class="service-cta">
        <span class="cta-icon"><svg width="32" height="32" viewBox="0 0 24 24"><path fill="#e3373d" d="M6.6 10.8a15 15 0 0 0 6.6 6.6l2.2-2.2c.3-.3.7-.4 1-.2 1.1.4 2.3.6 3.6.6.6 0 1 .4 1 1V20c0 .6-.4 1-1 1A17 17 0 0 1 3 4c0-.6.4-1 1-1h3.5c.6 0 1 .4 1 1 0 1.3.2 2.5.6 3.6.1.3 0 .7-.2 1z"/></svg></span>
        <div class="num">123 456 7890</div>
        <a class="btn" href="#">Contact Us Know</a>
      </div>
    </div>
  </div>
</section>

<section class="introducers">
  <div class="wrap">
    <h2 class="section-title">Our <span>Introducers</span></h2>
    <h3>WHY BECOME AN INTRODUCER ?</h3>
    <p>It has survived not only five centuries. Lorem Ipsum is simply dummy text of the printing and typesetting industry. Lorem Ipsum has been the industry's standard dummy text ever since the 1500s, when an unknown printer took a galley of type and scrambled it to make a type specimen book. It has survived not only five centuries.</p>
    <a class="btn btn--ghost" href="#">Know More</a>
  </div>
</section>

<section class="info">
  <div class="wrap">
    <div class="about">
      <h2>About <span class="accent">Us</span></h2>
      <p>It has survived not only five centuries. Lorem Ipsum is simply dummy text of the printing and typesetting industry.</p>
      <p>Lorem Ipsum is simply dummy text of the printing and typesetting industry. Lorem Ipsum has been the industry's standard dummy text ever since the 1500s, when an unknown printer took a galley of type and scrambled it to make a type specimen book.</p>
      <p>Lorem Ipsum has been the industry's standard dummy text ever since the 1500s, when an unknown printer took a galley of type and scrambled it to make a type specimen book. It has survived not only five centuries.</p>
      <a class="btn" href="#">Know More</a>
    </div>
    <div class="contact">
      <h2>Contact <span class="accent">Us</span></h2>
      <div class="field">Name <svg width="16" height="16" viewBox="0 0 16 16"><circle cx="8" cy="5" r="3.5" fill="#999"/><path d="M1 16c0-4 3-6 7-6s7 2 7 6z" fill="#999"/></svg></div>
      <div class="field">Email <svg width="16" height="16" viewBox="0 0 24 24"><path fill="#999" d="M6.6 10.8a15 15 0 0 0 6.6 6.6l2.2-2.2c.3-.3.7-.4 1-.2 1.1.4 2.3.6 3.6.6.6 0 1 .4 1 1V20c0 .6-.4 1-1 1A17 17 0 0 1 3 4c0-.6.4-1 1-1h3.5c.6 0 1 .4 1 1 0 1.3.2 2.5.6 3.6.1.3 0 .7-.2 1z"/></svg></div>
      <div class="field">Phone <svg width="18" height="14" viewBox="0 0 18 14"><rect width="18" height="14" rx="1" fill="#999"/><path d="M1 1l8 6 8-6" stroke="#fff" stroke-width="1.5" fill="none"/></svg></div>
      <div class="field field--message">Message <svg width="18" height="16" viewBox="0 0 18 16"><ellipse cx="7" cy="6" rx="7" ry="5" fill="#999"/><ellipse cx="12" cy="10" rx="6" ry="4.5" fill="#aaa"/></svg></div>
      <a class="btn" href="#">Submit</a>
    </div>
  </div>
</section>

<footer class="site-footer">
  <div class="wrap">
    <div class="footer-top">
      <ul class="footer-nav">
        <li class="is-active"><a href="#">Home</a></li>
        <li><a href="#">About Us</a></li>
        <li><a href="#">Services</a></li>
        <li><a href="#">Introducers</a></li>
        <li><a href="#">Contact Us</a></li>
      </ul>
      <div class="social"><span></span><span></span><span></span></div>
    </div>
    <div class="footer-head">Get in Toch</div>
    <div class="footer-contacts">
      <div class="fc"><span class="fc-icon fc-icon--solid"><svg width="22" height="26" viewBox="0 0 22 26"><path fill="#e3373d" d="M11 0a9 9 0 0 0-9 9c0 7 9 17 9 17s9-10 9-17a9 9 0 0 0-9-9zm0 12.5A3.5 3.5 0 1 1 11 5.5a3.5 3.5 0 0 1 0 7z"/></svg></span>101 - Lorem Ipsum is the<br>simple dummy text.</div>
      <div class="fc"><span class="fc-icon"><svg width="22" height="22" viewBox="0 0 24 24"><path fill="#fff" d="M6.6 10.8a15 15 0 0 0 6.6 6.6l2.2-2.2c.3-.3.7-.4 1-.2 1.1.4 2.3.6 3.6.6.6 0 1 .4 1 1V20c0 .6-.4 1-1 1A17 17 0 0 1 3 4c0-.6.4-1 1-1h3.5c.6 0 1 .4 1 1 0 1.3.2 2.5.6 3.6.1.3 0 .7-.2 1z"/></svg></span>123 456 7890</div>
      <div class="fc"><span class="fc-icon"><svg width="22" height="16" viewBox="0 0 18 14"><rect width="18" height="14" rx="1" fill="#fff"/><path d="M1 1l8 6 8-6" stroke="#e3373d" stroke-width="1.5" fill="none"/></svg></span>info@merrow.example</div>
      <div class="copy">© 2016 <b>MERROW</b> - All rights reserved.</div>
    </div>
  </div>
</footer>

</body>
</html>
```